Web Design for an Innovative Life Science Marketplace

IMPORTANT:
The software is called CS-Cart. It has capabilities and limitations with design features in the software. There is a certain framework that needs to be followed. It is PHP and Linux. It may require add-ons for your design, so please be specific with what is required. It’s preferred the designer has CS-Cart knowledge/experience.

Key Requirements
1. I’d like the design to include an implemented/recommended CS-Cart theme that is consistent with our branding (see the marketing collateral and logo).
2. I then need the additional design changes to that theme to create the below web pages.
3. All designs should be consistent with our branding. All pictures should either be computer generated (clip art-like) or pictures of happy patients. What is a happy patient? Close up photo of someone healthy, happy, and experiencing/enjoying life. Not someone in a hospital or getting care. Please see examples already on the site.

Please see the attached Web Design details in the word document. That document is important to complete the design.

```html
<!DOCTYPE html>
<html lang="en">
<head>
<meta charset="utf-8">
<title>CycleLink-LS — Life Science Marketplace</title>
<link href="https://fonts.googleapis.com/css2?family=Fira+Sans+Condensed:wght@500;600;700&family=Open+Sans:wght@400;600&display=swap" rel="stylesheet">
<style>
:root{
  --green:#8cc03f;
  --green-dark:#6fa32c;
  --teal:#2f7a63;
  --teal-deep:#256b57;
  --ink:#222;
  --text:#555;
  --muted:#777;
  --line:#d9d9d9;
  --soft:#f1f1f1;
  --white:#fff;
}
*{box-sizing:border-box;margin:0;padding:0}
html,body{width:1200px;height:2951px;overflow:hidden}
body{font-family:"Open Sans",sans-serif;color:var(--text);background:var(--white);position:relative}
.head-font{font-family:"Fira Sans Condensed",sans-serif}
section,header,footer{position:absolute;left:0;width:1200px}

/* header */
.site-header{top:0;height:146px;background:var(--white)}
.brand{position:absolute;left:79px;top:38px;display:flex;align-items:center;gap:12px}
.brand-dot{width:34px;height:34px;border-radius:50%;background:var(--green)}
.brand-name{font-family:"Fira Sans Condensed",sans-serif;font-weight:700;font-size:34px;color:var(--teal);letter-spacing:.5px}
.search{position:absolute;left:352px;top:26px;width:238px;height:31px;border:2px solid #999;border-radius:16px;padding:0 18px;font-size:14px;color:#999;font-style:italic;line-height:27px}
.search svg{position:absolute;right:14px;top:5px}
.util{position:absolute;top:30px;font-size:15px;color:#444;display:flex;align-items:center;gap:10px}
.util.cart{left:620px}
.util.account{left:767px}
.util-sep{position:absolute;left:745px;top:30px;width:1px;height:22px;background:#bbb}
.btn-contact{position:absolute;left:934px;top:20px;width:187px;height:41px;border-radius:21px;background:linear-gradient(90deg,var(--green),var(--teal));color:var(--white);font-family:"Fira Sans Condensed",sans-serif;font-weight:600;font-size:21px;text-align:center;line-height:41px}
.header-rule{position:absolute;left:350px;top:73px;width:771px;height:1px;background:var(--line)}
.nav{position:absolute;top:96px;left:0;font-size:15px;color:#444}
.nav a{position:absolute;white-space:nowrap;text-decoration:none;color:inherit}
.nav a.active{color:var(--teal)}

/* hero */
.hero{top:146px;height:572px;background:linear-gradient(100deg,#5a4a3a 0%,#8a7a63 28%,#b9b3a2 52%,#9aa08c 75%,#6d7a5e 100%)}
.hero-photo{position:absolute;inset:0}
.hero-panel{position:absolute;left:675px;top:0;width:417px;height:572px;background:rgba(240,240,238,.82)}
.hero-title{position:absolute;left:49px;top:130px;font-family:"Fira Sans Condensed",sans-serif;font-weight:600;font-size:38px;line-height:48px;color:var(--teal)}
.hero-copy{position:absolute;left:49px;top:247px;width:330px;font-size:14px;line-height:30px;color:#444}
.btn-pre{position:absolute;left:55px;top:388px;width:197px;height:47px;border-radius:24px;background:linear-gradient(90deg,var(--green),var(--teal));color:var(--white);font-family:"Fira Sans Condensed",sans-serif;font-weight:600;font-size:21px;text-align:center;line-height:47px}

/* who should join */
.join{top:718px;height:429px}
.section-title{font-family:"Fira Sans Condensed",sans-serif;font-weight:700;font-size:40px;color:var(--ink);text-align:center;position:absolute;left:0;width:1200px}
.join .section-title{top:54px}
.role-card{position:absolute;top:124px;height:206px;border:2px solid var(--green);background:var(--white);text-align:center}
.role-card.teal{border-color:var(--teal)}
.role-card .corner{position:absolute;left:0;top:0}
.role-card h3{font-family:"Open Sans",sans-serif;font-weight:400;font-size:22px;color:#333;margin-top:56px}
.role-card p{font-size:14px;line-height:26px;color:#555;margin:18px 22px 0}

/* about */
.about{top:1147px;height:446px;background:linear-gradient(90deg,#f0f0f0 0%,#f0f0f0 48%,#cfcabb 62%,#9e8e6e 100%)}
.about-photo{position:absolute;left:590px;top:0;width:610px;height:446px;background:linear-gradient(90deg,rgba(240,240,240,1) 0%,rgba(196,184,160,.6) 30%,rgba(150,130,100,.4) 100%)}
.about h2{position:absolute;left:79px;top:52px;font-family:"Fira Sans Condensed",sans-serif;font-weight:700;font-size:40px;color:var(--ink)}
.about p{position:absolute;left:79px;width:500px;font-size:14px;line-height:26px;color:#555}
.btn-know{position:absolute;left:79px;top:322px;width:199px;height:47px;border-radius:24px;background:linear-gradient(90deg,var(--green),var(--teal));color:var(--white);font-family:"Fira Sans Condensed",sans-serif;font-weight:600;font-size:21px;text-align:center;line-height:47px}

/* marketing band */
.marketing{top:1593px;height:292px;background:linear-gradient(90deg,var(--teal-deep),var(--green));text-align:center;color:var(--white)}
.marketing h2{position:absolute;top:52px;left:0;width:1200px;font-family:"Fira Sans Condensed",sans-serif;font-weight:600;font-size:40px}
.marketing p{position:absolute;top:112px;left:200px;width:800px;font-size:14px;line-height:26px}
.btn-light{position:absolute;top:187px;height:45px;border-radius:23px;background:var(--white);color:var(--green-dark);font-family:"Fira Sans Condensed",sans-serif;font-weight:600;font-size:20px;line-height:45px;text-align:center}

/* products */
.products{top:1885px;height:481px}
.products .section-title{top:52px}
.product{position:absolute;top:116px;width:260px;text-align:center}
.product .ring{display:block;margin:0 auto}
.product h3{font-family:"Open Sans",sans-serif;font-weight:400;font-size:22px;color:#333;margin-top:16px;line-height:33px}
.product p{font-size:14px;line-height:25px;color:#555;margin-top:6px}

/* partners */
.partners{top:2366px;height:230px;background:var(--soft)}
.partners h2{position:absolute;top:40px;left:0;width:1200px;text-align:center;font-weight:400;font-size:25px;color:#333}
.badge{position:absolute;top:82px;width:157px;height:94px;background:var(--white);border:1px solid var(--line)}
.badge span{position:absolute;left:36px;top:33px;width:85px;height:28px;border-radius:4px;background:#c9cfd3}

/* footer */
.site-footer{top:2596px;height:292px;background:var(--white)}
.foot-col{position:absolute;top:54px}
.foot-col h4{font-weight:400;font-size:21px;color:#333;margin-bottom:16px}
.foot-col ul{list-style:none}
.foot-col li{font-size:14px;color:#555;line-height:39px;display:flex;align-items:center;gap:14px}
.foot-col li::before{content:"";width:10px;height:10px;border-radius:50%;background:var(--green)}
.contact-line{display:flex;gap:16px;font-size:14px;color:#555;line-height:26px;margin-bottom:14px}
.contact-line svg{flex:none;margin-top:4px}
.bottom-bar{position:absolute;left:0;top:2888px;width:1200px;height:63px;background:linear-gradient(90deg,var(--teal-deep),var(--green));color:var(--white);font-size:14px;line-height:63px;padding-left:79px}
</style>
</head>
<body>

<header class="site-header">
  <div class="brand"><span class="brand-dot"></span><span class="brand-name">CYCLELINK-LS</span></div>
  <div class="search">Search...
    <svg width="20" height="20" viewBox="0 0 20 20"><circle cx="8" cy="8" r="6" fill="none" stroke="#444" stroke-width="2"/><line x1="12.5" y1="12.5" x2="18" y2="18" stroke="#444" stroke-width="2"/></svg>
  </div>
  <div class="util cart">
    <svg width="24" height="20" viewBox="0 0 24 20"><path d="M1 3h4l3 11h12l3-8H7" fill="none" stroke="#444" stroke-width="2"/><circle cx="10" cy="18" r="1.6" fill="#444"/><circle cx="18" cy="18" r="1.6" fill="#444"/></svg>
    MY CART</div>
  <span class="util-sep"></span>
  <div class="util account">
    <svg width="20" height="20" viewBox="0 0 20 20"><circle cx="10" cy="6" r="4.5" fill="#444"/><path d="M1 20c0-6 4-8 9-8s9 2 9 8z" fill="#444"/></svg>
    MY ACCOUNT</div>
  <div class="btn-contact">CONTACT US</div>
  <div class="header-rule"></div>
  <nav class="nav">
    <a class="active" style="left:350px">HOME</a>
    <a style="left:423px">ABOUT US</a>
    <a style="left:527px">WHY CYCLELINK-LS?</a>
    <a style="left:734px">OUR PARTNERS</a>
    <a style="left:875px">WHITE PAPER</a>
    <a style="left:999px">QUALITY POLICY</a>
  </nav>
</header>

<section class="hero">
  <div class="hero-photo" role="img" aria-label="Close-up photo of two happy young women hugging outdoors in autumn"></div>
  <div class="hero-panel">
    <h1 class="hero-title">JOIN THE CIRCULAR<br>SUPPLY CHAIN</h1>
    <p class="hero-copy">“A virtual multi-vendor marketplace and for the life sciences community to connect and transact before and after-market materials and equipment”</p>
    <div class="btn-pre">PRE- REGISTER</div>
  </div>
</section>

<section class="join">
  <h2 class="section-title">WHO SHOULD JOIN?</h2>
  <div class="role-card" style="left:79px;width:320px">
    <svg class="corner" width="110" height="70" viewBox="0 0 110 70"><polygon points="0,0 110,0 0,70" fill="var(--green)"/><circle cx="28" cy="22" r="11" fill="none" stroke="#fff" stroke-width="2"/><circle cx="28" cy="22" r="4" fill="#fff"/></svg>
    <h3>Manufacturers</h3>
    <p>Create an Account in Minutes to Sell/Buy Excess or Obsolete Materials and Equipment</p>
  </div>
  <div class="role-card teal" style="left:439px;width:322px">
    <svg class="corner" width="110" height="70" viewBox="0 0 110 70"><polygon points="0,0 110,0 0,70" fill="var(--teal)"/><circle cx="22" cy="16" r="4" fill="#fff"/><circle cx="34" cy="16" r="4" fill="#fff"/><path d="M15 32c0-6 4-9 7-9s7 3 7 9zM27 32c0-6 4-9 7-9s7 3 7 9z" fill="#fff"/></svg>
    <h3>Researchers</h3>
    <p>Sell/Buy Low-Cost Materials and Receive Donations</p>
  </div>
  <div class="role-card" style="left:799px;width:324px">
    <svg class="corner" width="110" height="70" viewBox="0 0 110 70"><polygon points="0,0 110,0 0,70" fill="var(--green)"/><path d="M16 14h5l4 14h12l3-10H23" fill="none" stroke="#fff" stroke-width="2"/><circle cx="27" cy="32" r="2" fill="#fff"/><circle cx="36" cy="32" r="2" fill="#fff"/></svg>
    <h3>Original Suppliers</h3>
    <p>Market Your Products Across a Broad Life Sciences Network</p>
  </div>
</section>

<section class="about">
  <div class="about-photo" role="img" aria-label="Photo of two laughing senior women sitting together on a park bench"></div>
  <h2>ABOUT US</h2>
  <p style="top:112px">We are a private and virtual B2B marketplace and consortium for life science manufacturers, researchers, and vendors to sell, purchase, and donate before and aftermarket materials and equipment as well as collaborate on non-financial ventures.</p>
  <p style="top:222px">We are in the developmental phase of our platform working with some of the most trusted and best industry partners.  We are tentatively scheduled for an exclusive launch before the end of 2018.</p>
  <div class="btn-know">KNOW MORE</div>
</section>

<section class="marketing">
  <h2>MAKRKETING MATERIALS</h2>
  <p>Lorem Ipsum is simply dummy text of the printing and typesetting industry. Lorem Ipsum has been the industry's standard dummy text ever since the 1500s, when an unknown printer took a galley of type.</p>
  <div class="btn-light" style="left:298px;width:291px">READ OUR WHITE PAPER</div>
  <div class="btn-light" style="left:610px;width:292px">READ OUR BROCHURE</div>
</section>

<section class="products">
  <h2 class="section-title">PRODUCTS</h2>
  <div class="product" style="left:63px">
    <svg class="ring" width="116" height="116" viewBox="0 0 116 116"><circle cx="58" cy="58" r="56" fill="none" stroke="var(--green)" stroke-width="2"/><circle cx="58" cy="58" r="47" fill="#fff" stroke="var(--green)" stroke-width="4"/><path d="M44 36h20l9 9v35H44z" fill="none" stroke="var(--teal)" stroke-width="3"/><rect x="40" y="52" width="36" height="16" fill="var(--teal)"/></svg>
    <h3>Raw Materials</h3>
    <p>Consumable and starting materials for API and intermediate manufacturing or research.</p>
  </div>
  <div class="product" style="left:338px">
    <svg class="ring" width="116" height="116" viewBox="0 0 116 116"><circle cx="58" cy="58" r="56" fill="none" stroke="var(--green)" stroke-width="2"/><circle cx="58" cy="58" r="47" fill="#fff" stroke="var(--green)" stroke-width="4"/><circle cx="58" cy="58" r="17" fill="none" stroke="var(--teal)" stroke-width="8" stroke-dasharray="7 6"/><circle cx="58" cy="58" r="7" fill="none" stroke="var(--teal)" stroke-width="3"/></svg>
    <h3>Equipment</h3>
    <p>End item systems manufactured for LS applications</p>
  </div>
  <div class="product" style="left:604px">
    <svg class="ring" width="116" height="116" viewBox="0 0 116 116"><circle cx="58" cy="58" r="56" fill="none" stroke="var(--green)" stroke-width="2"/><circle cx="58" cy="58" r="47" fill="#fff" stroke="var(--green)" stroke-width="4"/><rect x="40" y="40" width="16" height="16" fill="var(--teal)"/><rect x="60" y="40" width="16" height="16" fill="var(--teal)"/><rect x="40" y="60" width="16" height="16" fill="var(--teal)"/><rect x="60" y="60" width="16" height="16" fill="var(--teal)"/></svg>
    <h3>Parts</h3>
    <p>Components of a modular system used for LS applications</p>
  </div>
  <div class="product" style="left:873px">
    <svg class="ring" width="116" height="116" viewBox="0 0 116 116"><circle cx="58" cy="58" r="56" fill="none" stroke="var(--green)" stroke-width="2"/><circle cx="58" cy="58" r="47" fill="#fff" stroke="var(--green)" stroke-width="4"/><circle cx="58" cy="58" r="16" fill="none" stroke="var(--teal)" stroke-width="3"/><circle cx="58" cy="40" r="6" fill="var(--teal)"/><circle cx="42" cy="68" r="6" fill="var(--teal)"/><circle cx="74" cy="68" r="6" fill="var(--teal)"/></svg>
    <h3>Collaborative<br>Relationships</h3>
    <p>Safety Stock Agreements, Advertising/Selling/ Donating Capacity, joint supplier audits, etc.</p>
  </div>
</section>

<section class="partners">
  <h2>Our Partners</h2>
  <div class="badge" style="left:78px"><span></span></div>
  <div class="badge" style="left:256px"><span></span></div>
  <div class="badge" style="left:433px"><span></span></div>
  <div class="badge" style="left:612px"><span></span></div>
  <div class="badge" style="left:789px"><span></span></div>
  <div class="badge" style="left:966px"><span></span></div>
</section>

<footer class="site-footer">
  <div class="foot-col" style="left:79px">
    <h4>Our Marketplace</h4>
    <ul><li>About us</li><li>How it Works</li><li>Our Partners</li><li>White Paper</li></ul>
  </div>
  <div class="foot-col" style="left:441px">
    <h4>Customer service</h4>
    <ul><li>Quality Policy</li><li>Privacy Policy</li><li>Sign in</li></ul>
  </div>
  <div class="foot-col" style="left:803px">
    <h4>Contact Info</h4>
    <div class="contact-line">
      <svg width="18" height="24" viewBox="0 0 18 24"><path d="M9 23C4 16 1 12 1 8a8 8 0 0116 0c0 4-3 8-8 15z" fill="none" stroke="var(--teal)" stroke-width="1.8"/><circle cx="9" cy="8" r="3" fill="none" stroke="var(--teal)" stroke-width="1.8"/></svg>
      <span>240 Meridian Way STE 5<br>Harbor City, OH 44100</span></div>
    <div class="contact-line">
      <svg width="20" height="20" viewBox="0 0 20 20"><path d="M4 1l4 4-2 3c1 3 3 5 6 6l3-2 4 4-3 3C8 19 1 12 1 4z" fill="none" stroke="var(--teal)" stroke-width="1.8"/></svg>
      <span>+1 800-555-0142</span></div>
    <div class="contact-line">
      <svg width="22" height="16" viewBox="0 0 22 16"><rect x="1" y="1" width="20" height="14" fill="none" stroke="var(--teal)" stroke-width="1.8"/><path d="M1 1l10 8 10-8" fill="none" stroke="var(--teal)" stroke-width="1.8"/></svg>
      <span>hello@cyclelinkls.com</span></div>
  </div>
</footer>
<div class="bottom-bar">©CYCLELINK-LS. 2018 - All Rights Reserved.</div>

</body>
</html>
```